website design + images

We need a very appealing website design, layout and images for a sales analytics and sales productivity services company based in San Ramon, California. We need a good design for the home page and a template for all other pages (total 2 designs), and images for all inner pages (center column/banner images, and right hand top corner small images). There are about 18 inner pages.
Updates

Our existing website is www.brightvale.com
Our corporate colours are the ones that are there on the website. The logo is also shown. We will be changing the tagline to "accelerating revenue" or equivalent of that.

Please use the document "website for brightvale - template v2.doc" that I just uploaded for any reference to the content, navigation and wireframes. A few more clarifications are provided mainly for the link "Solutions".

Rajesh Kothuri

Hi,
We just uploaded ver 4 of the website template. There is more elaboration provided around the sublinks / sections for Solutions. Pls review and do get back if you need any clarifications.

Rgds
Rajesh Kothuri

Hi all,
We have so far received a few good designs. The designs are more or less on the right track. I would like to urge all of you to use the content and navigation provided in the document attached to our brief "website for brightvale - template v4.doc".  Please DO NOT use the content in our existing website www.brightvale.com . That is very old. We mentioned it only for reference to colour theme and broad details.

We have totally 13 sections in Solutions pages. They may be designed as a tree of links - first level sublinks - second level sublinks or links - first level sublinks and the remaining as sections within the first level sublinks pages. The page design would remain the same for all inner pages except careers. But after finalizing the design for the inner page, we will need images for the different inner pages.

Rgds
Rajesh Kothuri

Hi,
Thank you all for participation and very good designs. We are quite happy with what we have seen. We have now shortlisted about 4 vendors and sending invididual feedback to them for further improvement. We will be finalizing by Monday or Tuesday.  To the vendors who do not get feedback from us, thank you very much for participation. We may still do business in future for some of our other needs. 
The following are the process steps / expectations going forward, 
1. Feedback to the shortlisted designers and inviting improvements.
2. Review of the improved designs and further shortlist & feedback or direct finalization.
3. The design should be in 1024*768
2. Number of page designs = 2 (home page, inner page).
4. Home page design: instead of delivery model and customers, show one link "Why Us".
4. Solutions page design:  We will be needing an image in center column of solutions page that in a nutshell gives all the different types of solutions we provide. The entire set of solutions is in our attached document website for brightvale - template v4 and I am just uploading v5 with more description on sublinks.
5. After selection, we will be needing images for all the solution pages (total 12 pages under solutions + one solutions page), 1 image for Why Us?, 1 for Careers, and 3 for company (about us/ team, core values, ...) = total 18

Rgds
Rajesh Kothuri

Target Market(s)

We are a sales analytics and sales productivity services company. We help B2B companies with: sales planning; sales operations and sales measurement. The characteristics of our customers are:
- B2B medium enterprises (USD 100M- USD 2B in revenue) in the US
- Primary target verticals are: high-tech, engineering and professional services firms
- Our primary target customers titles are VP of Sales or VP of marketing; we could be selling to the CEO at companies with revenues below $200M

Industry/Entity Type

Consulting

Requirements
Must have
• - Clean, uncluttered design
• - Easy navigation; minimum clicks
Nice to have
• We have already built a content management system and wireframes for this site. To the extent possible, it would be great to leverage the wireframe structure we built, provided you don’t have to compromise on the look and feel and navigation of the site. Below is what we currently have as banner sizes and resolutions are:
• Home page banner size: 950 * 250’
• All pages – center top - image size: 558 * 160
• All pages – right hand top image – 175*135’

```html
<!DOCTYPE html>
<html lang="en">
<head>
<meta charset="utf-8">
<title>BrightVale – Solution</title>
<link href="https://fonts.googleapis.com/css2?family=Noto+Sans:wght@400;700&display=swap" rel="stylesheet">
<style>
:root{
  --ink:#222;
  --muted:#555;
  --teal:#17a7b5;
  --orange:#e0600f;
  --link:#1f5fa6;
  --nav-active:#1b5da8;
  --line:#c9c9c9;
  --band-top:#a9d0f3;
  --band-bottom:#2f78cb;
  --foot-top:#a6cdf4;
  --foot-bottom:#7fb3ea;
  --page:#f3f5f7;
  --green:#4f9a1c;
  --bullet:#d99a12;
  --brand:#1d6c8f;
}
*{box-sizing:border-box;margin:0;padding:0}
html,body{width:1200px;height:534px;overflow:hidden}
body{position:relative;font-family:"Noto Sans",Verdana,sans-serif;color:var(--ink);
  background:repeating-linear-gradient(135deg,var(--page) 0 3px,#fff 3px 6px)}
.header{position:absolute;left:0;top:0;width:1200px;height:77px;background:linear-gradient(#fff,#eef1f4)}
.brand{position:absolute;left:222px;top:24px;display:flex;align-items:center;gap:8px;
  font-size:25px;font-weight:700;color:var(--brand);letter-spacing:1px}
.brand-dot{width:14px;height:14px;border-radius:50%;background:var(--brand)}
.utility{position:absolute;left:760px;top:5px;width:236px;text-align:right;font-size:10.5px;color:#1c2f4a}
.main-nav{position:absolute;left:417px;top:49px;display:flex;gap:2px}
.main-nav a{display:block;height:26px;line-height:26px;text-align:center;font-size:13.5px;color:#111;
  text-decoration:none;background:linear-gradient(#fdfdfd,#e4e6e8);border:1px solid #d4d7da;border-bottom:none}
.main-nav a.active{color:var(--nav-active)}
.band{position:absolute;left:0;top:77px;width:1200px;height:115px;
  background:linear-gradient(var(--band-top),var(--band-bottom));box-shadow:0 2px 3px rgba(0,0,0,.25)}
.sidebar{position:absolute;left:206px;top:77px;width:161px;height:358px;background:#fff;
  border:1px solid var(--line);border-radius:4px}
.sidebar ul{list-style:none}
.sidebar li{position:absolute;white-space:nowrap}
.sidebar .top{left:24px;font-size:11px}
.sidebar .top::before{content:"";position:absolute;left:-13px;top:5px;width:5px;height:7px;
  border-left:1px dotted #777;border-right:1px dotted #777}
.sidebar .sub{left:27px;font-size:9.3px}
.sidebar .sub.wide{font-size:10.3px}
.sidebar .sub::before{content:"";position:absolute;left:-13px;top:6px;width:6px;border-top:1px dotted #888}
.sidebar .sub::after{content:"";position:absolute;left:-6px;top:3px;border:3px solid transparent;
  border-left:4px solid var(--green)}
.banner{position:absolute;left:374px;top:77px;width:622px;height:115px;
  background:linear-gradient(90deg,#cfe4f7,#e8f2fb 40%,#bfdcf5);border-radius:4px 4px 0 0;overflow:hidden}
.banner-photo{position:absolute;left:0;top:0;width:126px;height:115px;background:linear-gradient(#e8ecef,#c8b79a)}
.banner-card{position:absolute;left:146px;top:13px;width:404px;height:81px;background:#fff;border-radius:8px;
  box-shadow:0 1px 4px rgba(0,0,0,.2);padding:11px 30px}
.banner-card h1{font-size:19px;color:var(--teal);font-weight:700;line-height:22px;margin-left:3px}
.banner-card p{font-size:10.2px;color:#666;line-height:15px;margin-top:3px;margin-left:10px}
.content{position:absolute;left:373px;top:205px;width:466px;height:230px;background:#fff;
  border:1px solid var(--line);border-radius:5px;padding:10px 12px}
.content h2{font-size:13.5px;color:var(--teal);font-weight:700}
.content p{font-size:10.4px;line-height:16.7px;letter-spacing:.38px;color:#444;text-align:justify;margin:4px 0 0 3px}
.content p b{color:#333}
.solution-list{list-style:none;margin:4px 0 0 3px}
.solution-list li{position:relative;padding-left:19px;font-size:10.8px;line-height:20px;letter-spacing:.5px;color:#333}
.solution-list li::before{content:"";position:absolute;left:0;top:4px;width:11px;height:11px;border-radius:50%;background:var(--bullet)}
.solution-list li::after{content:"";position:absolute;left:4px;top:7px;border:2.5px solid transparent;border-left:3.5px solid #fff}
.aside{position:absolute;left:848px;top:205px;width:146px;height:230px;background:#fff;
  border:1px solid var(--line);border-radius:5px;padding:6px 7px}
.aside h3{font-size:14.5px;font-weight:400;color:var(--orange);border-left:4px solid var(--orange);padding-left:8px;line-height:16px;margin-left:2px}
.aside-photo{margin-top:8px;width:131px;height:79px;border-radius:3px;background:linear-gradient(90deg,#e3d6c8,#e9eaec)}
.aside p{font-size:10.2px;line-height:16.7px;color:#444;margin-top:11px;letter-spacing:.2px}
.aside a{display:block;text-align:right;font-size:10.2px;color:var(--link);text-decoration:none}
.footer{position:absolute;left:0;top:446px;width:1200px;height:67px;
  background:linear-gradient(var(--foot-top),var(--foot-bottom));text-align:center;font-size:10.5px;line-height:67px;color:#1a1a1a}
</style>
</head>
<body>
<header class="header">
  <div class="brand"><span class="brand-dot"></span>BrightVale</div>
  <div class="utility">Sign in (register) | Contact us | Sitemap</div>
  <nav class="main-nav">
    <a style="width:89px" href="#">Home</a>
    <a style="width:89px" class="active" href="#">Solutions</a>
    <a style="width:121px" href="#">Delivery Model</a>
    <a style="width:89px" href="#">Customers</a>
    <a style="width:89px" href="#">Company</a>
    <a style="width:89px" href="#">Careers</a>
  </nav>
</header>

<div class="band"></div>

<aside class="sidebar">
  <ul>
    <li class="top" style="top:17px">Home</li>
    <li class="top" style="top:41px">Solutions</li>
    <li class="sub" style="top:62px">Sales Planning Analytics</li>
    <li class="sub" style="top:88px">Sales Productivity Center</li>
    <li class="sub" style="top:114px">Sales Measurement Analytics</li>
    <li class="top" style="top:137px;left:25px">Delivery Model</li>
    <li class="sub wide" style="top:160px">Analytics</li>
    <li class="sub wide" style="top:185px">Operations</li>
    <li class="top" style="top:208px;left:25px">Customers</li>
    <li class="sub wide" style="top:232px">About Us</li>
    <li class="sub wide" style="top:257px">Team</li>
    <li class="sub wide" style="top:282px">Core values</li>
    <li class="top" style="top:304px">Careers</li>
  </ul>
</aside>

<section class="banner">
  <div class="banner-photo" role="img" aria-label="Photo of a smiling businesswoman in an office"></div>
  <div class="banner-card">
    <h1>Solution</h1>
    <p>Lorem Ipsum is simply dummy text of the printing and typeset-<br>ting industry.</p>
  </div>
</section>

<main class="content">
  <h2>Solution</h2>
  <p><b>Lorem Ipsum is simply</b> dummy text of the printing and typesetting industry. Lorem Ipsum has been the industry's standard dummy text ever since the 1500s, when an unknown printer took a galley of type and scrambled it to make a type specimen book. It has survived not only five centuries, but also the leap into electronic type-setting, remaining essentially unchanged. It was popularised in the 1960s with the release of Pressline sheets containing Lorem Ipsum passages, and more recently with desktop publishing software like Quillset Layout</p>
  <ul class="solution-list">
    <li>Sales Planning Analytics</li>
    <li>Sales Productivity Centers</li>
    <li>Sales Measurement Analytics</li>
  </ul>
</main>

<aside class="aside">
  <h3>Consulting</h3>
  <div class="aside-photo" role="img" aria-label="Photo of a support consultant wearing a headset"></div>
  <p>BrightVale delivers cus-tomized solutions to address your biggest marketing and sales operations challenges.</p>
  <a href="#">Read more...</a>
</aside>

<footer class="footer">© 2010 BrightVale, Inc. | Contact Us | Sign in (register) | Contact us | Sitemap</footer>
</body>
</html>
```